Brightfen Business Card Redesign & Logo Update

We need to update our business cards to something more modern and fresh. Brightfen can provide the current color schemes and old design examples, but welcome creativity in helping us with this redesign. PLEASE NOTE that we no longer utilize the "tree" and/or "leaf" imagery in our branding. If able would apprecaite an update on the quality of our "words only" logo in Ai. / PNG formats too.

Target Market(s)

Investors, landowners, corporate partners, contractors

Industry/Entity Type

Environmental Restoration & Conservation

Contact Information for Business Card

Logo, persons name, title, mailing address, phone and email, website url

Font styles to use
Other font styles liked:
• Merriweather

Requirements
Nice to have
• Logo, persons name, title, mailing address, phone and email, website url, but open to ideams
Should not have
• No all back backgrounds

```html
<!DOCTYPE html>
<html lang="en">
<head>
<meta charset="utf-8">
<title>Brightfen Business Card</title>
<link href="https://fonts.googleapis.com/css2?family=Lato:wght@400;700;900&display=swap" rel="stylesheet">
<style>
  :root {
    --backdrop: #2e2e2e;
    --brand-green: #137b39;
    --bright-green: #2fe089;
    --accent-orange: #ec7c0c;
    --paper: #ffffff;
  }
  * { margin: 0; padding: 0; box-sizing: border-box; }
  html, body { width: 1200px; height: 1122px; overflow: hidden; }
  body {
    background: var(--backdrop);
    font-family: "Lato", sans-serif;
    display: flex;
    flex-direction: column;
    align-items: center;
    justify-content: center;
    gap: 40px;
  }
  .card {
    position: relative;
    width: 840px;
    height: 480px;
    overflow: hidden;
    box-shadow: 0 10px 30px rgba(0,0,0,0.45);
  }
  .card-front {
    background: var(--brand-green);
    display: flex;
    align-items: center;
    justify-content: center;
  }
  .wordmark-front {
    font-weight: 900;
    font-size: 110px;
    letter-spacing: 2px;
    text-transform: uppercase;
    color: var(--bright-green);
    line-height: 1;
  }
  .card-back { background: var(--paper); }
  .card-back .backdrop-shape { position: absolute; inset: 0; }
  .contact-block {
    position: absolute;
    left: 60px;
    top: 92px;
    color: var(--paper);
  }
  .person-name {
    font-weight: 900;
    font-size: 32px;
    letter-spacing: 1px;
    text-transform: uppercase;
    line-height: 1.1;
  }
  .person-title {
    font-size: 21px;
    margin-top: 4px;
    letter-spacing: 0.5px;
  }
  .contact-list {
    list-style: none;
    margin-top: 24px;
    margin-left: 22px;
    font-size: 18px;
    letter-spacing: 0.8px;
    line-height: 1.35;
  }
  .contact-list li { display: flex; align-items: flex-start; gap: 14px; }
  .contact-list li + li { margin-top: 4px; }
  .contact-list .address { margin-bottom: 10px; }
  .contact-icon { width: 18px; height: 18px; flex: none; margin-top: 3px; fill: var(--paper); }
  .wordmark-back {
    position: absolute;
    right: 40px;
    top: 150px;
    font-weight: 900;
    font-size: 50px;
    line-height: 1;
    letter-spacing: 1px;
    text-transform: uppercase;
    color: var(--brand-green);
  }
</style>
</head>
<body>

  <section class="card card-front">
    <div class="wordmark-front">Brightfen</div>
  </section>

  <section class="card card-back">
    <svg class="backdrop-shape" viewBox="0 0 840 480" width="840" height="480" aria-hidden="true">
      <path d="M0 0 H360 C320 120 360 190 430 250 C510 320 540 400 535 480 H0 Z" fill="var(--brand-green)"/>
      <path d="M384 0 C346 120 388 188 456 246 C534 312 566 400 560 480 L552 480 C554 404 524 330 448 262 C380 202 350 120 378 0 Z" fill="var(--accent-orange)"/>
    </svg>

    <div class="contact-block">
      <h1 class="person-name">Daniel Reyes</h1>
      <p class="person-title">Founder &amp; CEO</p>
      <ul class="contact-list">
        <li class="address">
          <svg class="contact-icon" viewBox="0 0 24 24"><path d="M12 2a7 7 0 0 0-7 7c0 5 7 13 7 13s7-8 7-13a7 7 0 0 0-7-7zm0 9.5A2.5 2.5 0 1 1 12 6.5a2.5 2.5 0 0 1 0 5z"/></svg>
          <span>123 Anywhere St<br>Any City, State 12345</span>
        </li>
        <li>
          <svg class="contact-icon" viewBox="0 0 24 24"><path d="M6.6 10.8a15 15 0 0 0 6.6 6.6l2.2-2.2a1 1 0 0 1 1-.25 11.4 11.4 0 0 0 3.6.57 1 1 0 0 1 1 1V20a1 1 0 0 1-1 1A17 17 0 0 1 3 4a1 1 0 0 1 1-1h3.5a1 1 0 0 1 1 1c0 1.25.2 2.45.57 3.57a1 1 0 0 1-.25 1z"/></svg>
          <span>(123) 456-7890</span>
        </li>
        <li>
          <svg class="contact-icon" viewBox="0 0 24 24"><path d="M7 1h10a2 2 0 0 1 2 2v18a2 2 0 0 1-2 2H7a2 2 0 0 1-2-2V3a2 2 0 0 1 2-2zm0 3v14h10V4zm5 15.5a1.2 1.2 0 1 0 0 2.4 1.2 1.2 0 0 0 0-2.4z"/></svg>
          <span>(123) 456-7890</span>
        </li>
        <li>
          <svg class="contact-icon" viewBox="0 0 24 24"><path d="M6 2h12v5H6zM4 8h16a2 2 0 0 1 2 2v7h-4v5H6v-5H2v-7a2 2 0 0 1 2-2zm4 7v5h8v-5z"/></svg>
          <span>(123) 456-7890</span>
        </li>
        <li>
          <svg class="contact-icon" viewBox="0 0 24 24"><path d="M2 5h20v14H2zm2 2v.5l8 5.5 8-5.5V7zm0 3v7h16v-7l-8 5.5z"/></svg>
          <span>hello@yourwebsite.com</span>
        </li>
        <li>
          <svg class="contact-icon" viewBox="0 0 24 24"><path d="M12 2a10 10 0 1 0 0 20 10 10 0 0 0 0-20zm6.9 6h-3a15 15 0 0 0-1.3-3.9A8 8 0 0 1 18.9 8zM12 4c.9 1.2 1.600 2.600 2 4h-4c.4-1.4 1.1-2.8 2-4zM4.3 14a8 8 0 0 1 0-4h3.4a16 16 0 0 0 0 4zm.8 2h3a15 15 0 0 0 1.3 3.9A8 8 0 0 1 5.1 16zm3-8h-3a8 8 0 0 1 4.3-3.9C8.8 5.3 8.4 6.6 8.1 8zM12 20c-.9-1.2-1.6-2.6-2-4h4c-.4 1.4-1.1 2.8-2 4zm2.3-6H9.7a14 14 0 0 1 0-4h4.6a14 14 0 0 1 0 4zm.3 5.9c.6-1.2 1-2.5 1.3-3.9h3a8 8 0 0 1-4.3 3.9zM16.3 14a16 16 0 0 0 0-4h3.4a8 8 0 0 1 0 4z"/></svg>
          <span>www.yourwebsite.com</span>
        </li>
      </ul>
    </div>

    <div class="wordmark-back">Brightfen</div>
  </section>

</body>
</html>
```